Unique Business Card Design

Unique Business Card design for our orthotic and prosthetic company. Our logo is on our website, color is light blue. Unique shape (artificial leg shaped, vertical, etc..) preferred. Logo, business name, individual name and basic demographics needed.

Industry/Entity Type

Business

Contact Information for Business Card

Logo, Industry, Phone # Logo, "Prosthetic & Orthotic Services" Place to add individual name and contact info

Colors
cee9f5

Requirements
Must have
• The icon must be there, placement of "Prosthetic & Orthotic Services" can be moved
Nice to have
• Like the mix of light blue, and a little darker blue. One design included the icons from my website which was a nice touch

```html
<!DOCTYPE html>
<html lang="en">
<head>
<meta charset="utf-8">
<title>Limbwell Inc – Business Card</title>
<link rel="stylesheet" href="https://fonts.googleapis.com/css2?family=Source+Sans+3:wght@400;600;700&family=Great+Vibes&display=swap">
<style>
  :root {
    --page-bg: #ece8e3;
    --card-bg: #d3eaf6;
    --brand-blue: #0c72cc;
    --swoosh-grey: #4a4c4f;
    --text-grey: #4b4b4b;
    --white: #ffffff;
  }
  * { margin: 0; padding: 0; box-sizing: border-box; }
  html, body { width: 1200px; height: 900px; overflow: hidden; }
  body {
    background: var(--page-bg);
    font-family: "Source Sans 3", Arial, sans-serif;
    position: relative;
  }
  .card {
    position: absolute;
    width: 520px;
    height: 297px;
    background: var(--card-bg);
    overflow: hidden;
    box-shadow: 0 6px 18px rgba(0,0,0,0.18);
  }
  .card-front { left: 90px; top: 150px; }
  .card-back { left: 590px; top: 460px; }

  /* Front */
  .front-mark {
    position: absolute;
    left: 58px; top: 96px;
    width: 104px; height: 104px;
    border-radius: 50%;
    background: var(--brand-blue);
  }
  .brand-block {
    position: absolute;
    left: 190px; top: 108px;
  }
  .brand-name {
    color: var(--brand-blue);
    font-weight: 600;
    font-size: 31px;
    letter-spacing: 0.5px;
    line-height: 1;
    padding-bottom: 6px;
    border-bottom: 2px solid var(--brand-blue);
  }
  .brand-tagline {
    font-family: "Great Vibes", cursive;
    color: var(--brand-blue);
    font-size: 19px;
    margin-top: 4px;
    padding-left: 26px;
  }

  /* Back */
  .back-wave { position: absolute; left: 0; top: 0; }
  .back-mark {
    position: absolute;
    left: 358px; top: 12px;
    width: 136px; height: 124px;
    border-radius: 50%;
    background: var(--brand-blue);
  }
  .contact {
    position: absolute;
    left: 44px; top: 78px;
    color: var(--text-grey);
  }
  .person-name {
    color: var(--brand-blue);
    font-weight: 700;
    font-size: 19px;
    line-height: 1.1;
  }
  .person-role { font-size: 15px; margin-left: 6px; }
  .contact-lines { margin-top: 14px; margin-left: 14px; font-size: 15px; line-height: 1.35; }
  .contact-line { display: flex; align-items: center; gap: 6px; }
  .contact-line svg { width: 11px; height: 11px; fill: var(--brand-blue); }
  .phone { color: var(--brand-blue); font-weight: 600; }
  .address { margin-top: 18px; margin-left: 14px; font-size: 16px; line-height: 1.3; }
  .website {
    position: absolute;
    right: 22px; top: 196px;
    color: var(--white);
    font-size: 13px;
  }
</style>
</head>
<body>
  <section class="card card-front">
    <div class="front-mark"></div>
    <div class="brand-block">
      <div class="brand-name">LIMBWELL INC</div>
      <div class="brand-tagline">Prosthetic &amp; Orthotic Services</div>
    </div>
  </section>

  <section class="card card-back">
    <svg class="back-wave" width="520" height="297" viewBox="0 0 520 297">
      <path d="M0,262 C160,300 300,220 400,158 C450,128 490,118 520,112 L520,297 L0,297 Z" fill="var(--brand-blue)"/>
      <path d="M0,232 C150,270 290,215 410,150 C300,212 160,268 0,252 Z" fill="var(--swoosh-grey)"/>
    </svg>
    <div class="back-mark"></div>
    <div class="contact">
      <div class="person-name">Daniel Harper</div>
      <div class="person-role">Managing Director</div>
      <div class="contact-lines">
        <div class="contact-line phone">
          <svg viewBox="0 0 12 12"><path d="M2.5 1 L4.5 1 L5 3.5 L3.8 4.4 C4.5 6 6 7.5 7.6 8.2 L8.5 7 L11 7.5 L11 9.5 C11 10.4 10.3 11 9.5 11 C5 11 1 7 1 2.5 C1 1.7 1.6 1 2.5 1 Z"/></svg>
          <span>(555) 014-2290</span>
        </div>
        <div class="contact-line">
          <svg viewBox="0 0 12 12"><path d="M1 2.5 H11 V9.5 H1 Z M1.6 3 L6 6.5 L10.4 3" stroke="#d3eaf6" stroke-width="0.8"/></svg>
          <span>info@limbwellinc.com</span>
        </div>
      </div>
      <div class="address">1234, Address GoesHere,<br>Country, 12345</div>
    </div>
    <div class="website">www.limbwellinc.com</div>
  </section>
</body>
</html>
```